Need business card with a logo for a hearing aid sales and audiology business. We have two Hearing Instrument Specialists and one Audiologist on staff. Over 25 years in business. Locally owned and operated. Financing available. Most insurances accepted.

Summit Audio Wellness LLC
48730 W Larchmont, Suite 7
Spokane, WA 99281
509-617-2084
www.summitaudiowell.example

Manager
Tobias Kerrell HIS COHC
License #71829046

Target Market(s)

50yr old + people with a hearing loss.

Industry/Entity Type

Business

Contact Information for Business Card

48730 W Larchmont, Suite 7
Spokane, WA 99281
509-617-2084
www.summitaudiowell.example

Manager
Tobias Kerrell HIS COHC
NLVE #71829046

Font styles to use
Serif
Sans Serif

Requirements
Must have
• Business name, Tobias's name and title(s) and contact information, License #, web address

```html
<!DOCTYPE html>
<html lang="en">
<head>
<meta charset="utf-8">
<title>Summit Audio Wellness – Business Card</title>
<link href="https://fonts.googleapis.com/css2?family=Open+Sans:wght@400;600;700&display=swap" rel="stylesheet">
<style>
  :root {
    --backdrop: #e9e6e2;
    --card: #ffffff;
    --brand-blue: #1e4595;
    --band-dark: #1f4a9a;
    --band-light: #1667c2;
    --ink: #2e2e2e;
    --rule: #c9c9c9;
    --photo-light: #f6f0ea;
    --photo-mid: #e8ddd3;
  }
  * { margin: 0; padding: 0; box-sizing: border-box; }
  html, body {
    width: 1200px; height: 1000px; overflow: hidden;
    background: var(--backdrop);
    font-family: "Open Sans", Arial, sans-serif;
    color: var(--ink);
  }
  .canvas { position: relative; width: 1200px; height: 1000px; }
  .card {
    position: absolute; left: 265px; width: 666px; height: 398px;
    background: var(--card); overflow: hidden;
    box-shadow: 0 2px 6px rgba(0,0,0,0.18);
  }
  .card--front { top: 73px; }
  .card--back { top: 531px; }

  .brand {
    position: absolute; display: flex; align-items: center; gap: 12px;
    color: var(--brand-blue); font-weight: 600; line-height: 1.05;
  }
  .brand__dot { width: 22px; height: 22px; border-radius: 50%; background: var(--brand-blue); flex: none; }
  .card--front .brand { right: 32px; top: 52px; font-size: 34px; }
  .card--back .brand { left: 33px; top: 268px; font-size: 36px; z-index: 2; }

  .person { position: absolute; left: 33px; top: 197px; }
  .person__name { font-size: 19px; font-weight: 700; color: var(--brand-blue); letter-spacing: 0.2px; }
  .person__creds { font-size: 15px; font-weight: 400; margin-left: 3px; }
  .person__role { font-size: 15.5px; margin-top: 1px; }
  .divider { position: absolute; left: 33px; top: 248px; width: 452px; height: 1px; background: var(--rule); }
  .license { position: absolute; left: 33px; top: 268px; font-size: 15.5px; }

  .contact { position: absolute; right: 32px; top: 238px; text-align: right; font-size: 15.5px; line-height: 21px; }
  .contact__line { display: flex; justify-content: flex-end; align-items: center; gap: 6px; }
  .contact__icon { width: 16px; height: 16px; fill: var(--brand-blue); }
  .contact__business { font-weight: 700; margin-top: 4px; }

  .bands { position: absolute; left: 0; bottom: 0; width: 666px; height: 30px; }

  .photo {
    position: absolute; inset: 0;
    background: linear-gradient(90deg, var(--card) 0%, var(--card) 30%, var(--photo-light) 55%, var(--photo-mid) 100%);
  }
</style>
</head>
<body>
<div class="canvas">
  <section class="card card--front">
    <div class="brand"><span class="brand__dot"></span><span>Summit Audio<br>Wellness</span></div>

    <div class="person">
      <div><span class="person__name">TOBIAS KERRELL</span><span class="person__name person__creds">HIS COHC</span></div>
      <div class="person__role">Manager</div>
    </div>
    <div class="divider"></div>
    <div class="license">License #71829046</div>

    <div class="contact">
      <div class="contact__line">509-617-2084
        <svg class="contact__icon" viewBox="0 0 16 16"><path d="M2 6c0-2 3-3 6-3s6 1 6 3v1h-3V5.5H5V7H2z M4 8h8l1 5H3z"/></svg>
      </div>
      <div class="contact__line">www.summitaudiowell.example
        <svg class="contact__icon" viewBox="0 0 16 16"><circle cx="8" cy="8" r="7"/><path d="M9 7l5 5-2 0 1 2-1 .5-1-2-2 1.5z" fill="#fff"/></svg>
      </div>
      <div class="contact__business">Summit Audio Wellness</div>
      <div>48730 W Larchmont, Suite 7</div>
      <div>Spokane, WA 99281</div>
    </div>

    <svg class="bands" viewBox="0 0 666 30" aria-hidden="true">
      <polygon points="0,12 320,12 306,30 0,30" fill="var(--band-dark)"/>
      <polygon points="345,0 666,0 666,30 318,30" fill="var(--band-light)"/>
    </svg>
  </section>

  <section class="card card--back">
    <div class="photo" role="img" aria-label="Soft close-up photo of an older person wearing a behind-the-ear hearing aid and glasses"></div>
    <div class="brand"><span class="brand__dot"></span><span>Summit Audio<br>Wellness</span></div>
  </section>
</div>
</body>
</html>
```